"Inkvale" printing shop

-The design must be based around the attached HPID (home page information design) called "Inkvale - HPID".

The table boxes are just for approximate placement of information – you DON'T have to box everything in and you can arrange these. All fonts used in the HPID are only examples - you can use any Google font you wish.

- Information only is in orange text. Copy to go on the design in black text. Some instructions are in the HPID. Please be creative!

-The design needs to be modern. Colours are to be consistent with their new logo or complement it. Keep it clean and simple, you don't need to use lots of colours. Use lots of white.

- images / icons for the site need to be relevant and high quality, but they must also be free images or icons. I have attached a few examples that could be used.

Width of content will be 1100 pixels when implemented as a web page. Header height (without nav bar) 150-200 pixels.

If your design is chosen the winning PSD file will have to be provided as follows…
1. Canvas size of 2000px x 2000px - 72ppi in Adobe Photoshop (CS5 compatible)
2. Width of content section is 1100px wide - centered in the canvas
3. Any button rollovers/hovers in the PSD as hidden layers.
4. All fonts used must be Google fonts.
5. You will need to supply the chosen home page plus one example page (example page as a style guide for how all other pages will look). Example page is only the header and navigational bar at the top, an empty sector in the middle with a column (190 px wide) which can be left or right aligned which means the main sector is 910 pixels wide, and then the footer at the bottom of the page

Checklist - http://pagebuildertally.example/

Examples of some websites that have great design... don't copy them please but they are similar in look to what we are after....
http://www.rookfenly.example/

Industry/Entity Type

Printing

Font styles to use
Serif
Sans Serif

Requirements
Should not have
• Drop shadows, comic sans font

```html
<!DOCTYPE html>
<html lang="en">
<head>
<meta charset="utf-8">
<title>Inkvale – Printing, Laminating and Photocopying</title>
<link href="https://fonts.googleapis.com/css2?family=Roboto+Condensed:wght@400;700&family=Roboto:wght@400;500;700&display=swap" rel="stylesheet">
<style>
:root{
  --blue:#1a8ac9;
  --blue-dark:#0f6aa0;
  --ink:#1f2a33;
  --grey-bg:#dcdcdc;
  --tile:#ececec;
  --text:#333;
  --muted:#777;
  --footer:#2b2b2b;
  --footer-text:#bbb;
  --white:#fff;
}
*{box-sizing:border-box;margin:0;padding:0}
html,body{width:684px;height:1200px;overflow:hidden;background:var(--white)}
body{font-family:"Roboto",Arial,sans-serif;color:var(--text);position:relative}

/* header */
.site-header{position:absolute;top:0;left:0;width:684px;height:91px}
.brand{position:absolute;left:12px;top:14px;display:flex;align-items:center;gap:6px;width:190px}
.brand-mark{width:40px;height:40px;border-radius:50%;background:var(--blue);flex:none}
.brand-name{font-family:"Roboto Condensed",sans-serif;font-weight:700;font-size:28px;line-height:1;color:var(--ink);white-space:nowrap}
.tagline{position:absolute;left:220px;top:16px;width:290px}
.tagline h1{font-family:"Roboto Condensed",sans-serif;font-weight:700;font-size:17px;line-height:1.1;color:var(--blue);letter-spacing:.3px;white-space:nowrap}
.tagline p{font-size:7.5px;color:var(--muted);margin-top:5px;white-space:nowrap}
.top-links{position:absolute;right:14px;top:4px;display:flex;gap:10px;font-size:7.5px;color:var(--text)}
.contact{position:absolute;right:14px;top:26px;width:140px;font-size:8px;color:var(--text)}
.contact div{display:flex;align-items:center;gap:6px;margin-bottom:6px}
.contact svg{flex:none}

/* nav */
.main-nav{position:absolute;top:91px;left:0;width:684px;height:16px;background:var(--blue);display:flex;align-items:center;padding-left:8px;gap:11px}
.main-nav a{font-size:7.5px;color:var(--white);text-decoration:none;white-space:nowrap}

/* hero */
.hero{position:absolute;top:107px;left:0;width:684px;height:223px;background:linear-gradient(120deg,#8a6f5a 0%,#4f5a66 35%,#7a4a3e 60%,#3c4650 100%)}
.hero h2{position:absolute;left:150px;top:84px;width:440px;font-family:"Roboto Condensed",sans-serif;font-weight:700;font-size:25px;line-height:1.12;color:var(--white);text-transform:uppercase}

/* services tiles */
.tiles{position:absolute;top:330px;left:0;width:684px;height:332px;background:var(--grey-bg)}
.tile{position:absolute;width:120px;height:120px;background:var(--tile);display:flex;flex-direction:column;align-items:center;justify-content:center;gap:18px}
.tile span{font-family:"Roboto Condensed",sans-serif;font-size:12px;color:var(--ink);text-transform:uppercase;white-space:nowrap}
.tile svg{width:34px;height:34px}

/* features */
.features{position:absolute;top:676px;left:132px;width:420px;display:grid;grid-template-columns:1fr 1fr;column-gap:18px;row-gap:22px}
.feature{display:flex;gap:8px}
.feature-icon{flex:none;width:30px;height:30px;border-radius:50%;background:var(--blue);display:flex;align-items:center;justify-content:center}
.feature h3{font-size:8px;font-weight:700;color:var(--ink);margin-bottom:2px}
.feature p{font-size:5.6px;line-height:1.35;color:var(--muted)}
.feature .more{font-size:6px;color:var(--blue);text-align:right;display:block}

/* quote */
.quote{position:absolute;top:890px;left:0;width:684px;height:190px;border-top:1px solid #e6e6e6}
.quote h2{position:absolute;left:72px;top:12px;font-family:"Roboto Condensed",sans-serif;font-weight:700;font-size:14px;color:var(--ink)}
.quote .intro{position:absolute;left:72px;top:34px;width:100px;font-size:6px;line-height:1.4;color:var(--muted)}
.quote .upload{position:absolute;left:72px;top:96px;width:100px;font-size:6px;line-height:1.4;color:var(--muted)}
.field{position:absolute;height:16px;border:1px solid #d6d6d6;font-size:6px;color:#aaa;padding:4px 5px}
.submit{position:absolute;left:548px;top:157px;width:50px;height:14px;background:var(--blue);color:var(--white);font-size:7px;text-align:center;line-height:14px}

/* footer */
.site-footer{position:absolute;top:1088px;left:0;width:684px;height:112px;background:var(--footer);color:var(--footer-text)}
.site-footer h2{position:absolute;left:72px;top:12px;font-family:"Roboto Condensed",sans-serif;font-size:12px;color:var(--white);font-weight:700}
.footer-links{position:absolute;left:72px;top:38px;display:flex;gap:9px;font-size:6.4px;white-space:nowrap}
.footer-bottom{position:absolute;left:72px;right:72px;top:86px;border-top:1px solid #444;padding-top:6px;display:flex;justify-content:space-between;align-items:center;font-size:6px}
.social{display:flex;align-items:center;gap:4px}
.social i{width:12px;height:12px;border-radius:50%;background:#ddd;display:block}
</style>
</head>
<body>

<header class="site-header">
  <div class="brand"><div class="brand-mark"></div><div class="brand-name">Inkvale</div></div>
  <div class="tagline">
    <h1>DUPLICATION IS OUR VOCATION</h1>
    <p>Professional Photocopying · Digital &amp; Film Processing, Design &amp; Printing</p>
  </div>
  <nav class="top-links"><span>Home</span><span>About</span><span>Free Quote</span><span>Contact</span></nav>
  <div class="contact">
    <div><svg width="12" height="12" viewBox="0 0 12 12"><circle cx="6" cy="6" r="6" fill="#1a8ac9"/><path d="M4 3.5l1 1-.6.9a4 4 0 0 0 2 2l.9-.6 1 1-.7.8c-2 0-4.2-2.2-4.3-4.3z" fill="#fff"/></svg>07 555 0148</div>
    <div><svg width="12" height="12" viewBox="0 0 12 12"><circle cx="6" cy="6" r="6" fill="#1a8ac9"/><path d="M6 2.8a2 2 0 0 0-2 2c0 1.5 2 4 2 4s2-2.5 2-4a2 2 0 0 0-2-2z" fill="#fff"/></svg>12 Harbour Lane, Westside, Tauranga</div>
  </div>
</header>

<nav class="main-nav">
  <a>Photocopying</a><a>Printing</a><a>Laminating</a><a>Business cards</a><a>Typing services</a><a>Film processing</a><a>Photo Printing</a><a>Passport Photos</a><a>Image Restoration</a><a>Printer Supplies</a>
</nav>

<section class="hero" role="img" aria-label="Photograph of printed brochures and colour prints spread on a table">
  <h2>Digital printing, laminating and photocopying services throughout Tauranga</h2>
</section>

<section class="tiles">
  <div class="tile" style="left:132px;top:28px">
    <svg viewBox="0 0 34 34" fill="none" stroke="#1f2a33" stroke-width="2"><path d="M4 12l13-6 13 6-13 6z"/><path d="M4 18l13 6 13-6"/><path d="M4 24l13 6 13-6"/></svg>
    <span>Photo Copying</span></div>
  <div class="tile" style="left:282px;top:28px">
    <svg viewBox="0 0 34 34" fill="none" stroke="#1f2a33" stroke-width="2"><rect x="6" y="5" width="22" height="26"/><path d="M10 3v5M14 3v5M18 3v5M22 3v5M10 15h14M10 20h14M10 25h10"/></svg>
    <span>Laminating &amp; Binding</span></div>
  <div class="tile" style="left:432px;top:28px">
    <svg viewBox="0 0 34 34" fill="#1f2a33"><rect x="9" y="3" width="16" height="9" fill="none" stroke="#1f2a33" stroke-width="2"/><rect x="3" y="12" width="28" height="12" rx="2"/><rect x="9" y="20" width="16" height="11" fill="#fff" stroke="#1f2a33" stroke-width="2"/></svg>
    <span>Digital Printing</span></div>
  <div class="tile" style="left:132px;top:183px">
    <svg viewBox="0 0 34 34" fill="none" stroke="#1f2a33" stroke-width="2"><rect x="7" y="3" width="20" height="28"/><path d="M7 8h4M7 14h4M7 20h4M7 26h4M23 8h4M23 14h4M23 20h4M23 26h4"/></svg>
    <span>Film Processing</span></div>
  <div class="tile" style="left:282px;top:183px">
    <svg viewBox="0 0 34 34" fill="none" stroke="#1f2a33" stroke-width="2"><rect x="3" y="7" width="28" height="20" rx="2"/><circle cx="12" cy="15" r="3"/><path d="M7 23c1-4 9-4 10 0M20 13h7M20 18h7M20 22h5"/></svg>
    <span>Business Cards</span></div>
  <div class="tile" style="left:432px;top:183px">
    <svg viewBox="0 0 34 34" fill="#1f2a33"><rect x="3" y="10" width="28" height="14" rx="2"/><rect x="10" y="4" width="14" height="8" fill="#fff" stroke="#1f2a33" stroke-width="2"/><rect x="9" y="19" width="16" height="12" fill="#fff" stroke="#1f2a33" stroke-width="2"/><path d="M11 29l4-5 3 3 2-2 3 4z"/></svg>
    <span>Photo Printing</span></div>
</section>

<section class="features">
  <div class="feature"><div class="feature-icon"><svg width="16" height="16" viewBox="0 0 16 16" fill="#fff"><rect x="2" y="6" width="12" height="6"/><rect x="4" y="2" width="8" height="3"/></svg></div>
    <div><h3>Cost Effective Photocopying</h3><p>Sharp, clean copies in black and white or colour, from a single page to large runs, done while you wait.</p><span class="more">Click Here »</span></div></div>
  <div class="feature"><div class="feature-icon"><svg width="16" height="16" viewBox="0 0 16 16" fill="#fff"><rect x="2" y="3" width="12" height="8"/><rect x="6" y="11" width="4" height="2"/></svg></div>
    <div><h3>Personal Desktop Publishing</h3><p>From personalised brochures, posters and letterheads to special occasion cards, we design and print it all.</p><span class="more">Click Here »</span></div></div>
  <div class="feature"><div class="feature-icon"><svg width="16" height="16" viewBox="0 0 16 16" fill="#fff"><rect x="2" y="6" width="12" height="5"/><rect x="4" y="9" width="8" height="5"/></svg></div>
    <div><h3>All Digital Format Printing</h3><p>Bring in your files on a stick or email them to us and we can print at the size you need.</p><span class="more">Click Here »</span></div></div>
  <div class="feature"><div class="feature-icon"><svg width="16" height="16" viewBox="0 0 16 16" fill="#fff"><rect x="4" y="2" width="8" height="12"/></svg></div>
    <div><h3>Film Photo Processing</h3><p>Bring your film to the store and we will process it and return quality prints in a few days.</p><span class="more">Click Here »</span></div></div>
  <div class="feature"><div class="feature-icon"><svg width="16" height="16" viewBox="0 0 16 16" fill="#fff"><rect x="3" y="2" width="10" height="12"/></svg></div>
    <div><h3>Laminating &amp; Binding</h3><p>Protect your menus, signs and certificates with tough laminating and neat binding for reports.</p><span class="more">Click Here »</span></div></div>
  <div class="feature"><div class="feature-icon"><svg width="16" height="16" viewBox="0 0 16 16" fill="#fff"><rect x="2" y="3" width="12" height="10"/></svg></div>
    <div><h3>Quality Digital Photo Print</h3><p>Get your photos printed to your requirements from a file or from your digital camera card.</p><span class="more">Click Here »</span></div></div>
</section>

<section class="quote">
  <h2>Get A Free Quote</h2>
  <p class="intro">...or talk to our team about your requirements. Please fill out the form below and we will contact you within a day.</p>
  <p class="upload">You can now upload and send us your file for a free quote!</p>
  <div class="field" style="left:248px;top:14px;width:170px">First Name</div>
  <div class="field" style="left:248px;top:37px;width:170px">Last Name</div>
  <div class="field" style="left:248px;top:60px;width:170px">Phone Number</div>
  <div class="field" style="left:428px;top:14px;width:170px">Email</div>
  <div class="field" style="left:428px;top:37px;width:170px;height:108px">Message</div>
  <div class="submit">Submit</div>
</section>

<footer class="site-footer">
  <h2>Quick Links</h2>
  <nav class="footer-links">
    <span>» Home</span><span>» About</span><span>» Photocopying</span><span>» Printing</span><span>» Laminating</span><span>» Business Cards</span><span>» Typing Services</span><span>» Film Processing</span><span>» Photo Printing</span>
  </nav>
  <div class="footer-links" style="top:52px">
    <span>» Passport Photos</span><span>» Image Restoration</span><span>» Printer Supplies</span><span>» Free Quote</span><span>» Contact</span>
  </div>
  <div class="footer-bottom">
    <span>Copyright by Inkvale, 2015</span>
    <div class="social"><span>Follow Us</span><i></i><i></i><i></i><i></i></div>
  </div>
</footer>

</body>
</html>
```